Website Design for WestaKolory.pl – Luxury Wedding Car Rental with Chauffeur

We are looking for a talented designer to create a modern, elegant, and fully responsive website for our new brand – WestyKolory.pl. We are a premium car rental platform in Poland, offering luxury and exotic vehicles exclusively for weddings. All cars come with a professional chauffeur, ensuring a high-end, stress-free, and stylish experience.
Website Purpose:
The website should present our offering in a luxurious, clear, and inspiring way. It must build trust, highlight the prestige of our brand, and encourage inquiries. Our target audience includes engaged couples, wedding planners, and clients seeking a truly exceptional vehicle for their special day.
Design Requirements:
Style: modern, elegant, minimalist
Color palette: white, black, gold, optionally silver – refined and luxurious
Typography: clean, modern, high-end
Layout: clear, intuitive, with large car images and well-defined sections
Fully responsive (desktop, tablet, mobile)
Bilingual layout (Polish/English) must be considered
Pages to Design:
Homepage
About Us
Fleet Overview
Individual Car Pages
Services (Weddings, Photo Shoots, Film Rentals)
Why Us / Unique Selling Points
Contact
FAQ
Inspiration:
Luxury automotive brands (e.g. Varnel-Hoske, Corvash, Elbrin Tusko)
High-end wedding websites
Minimalist layouts with large visuals and elegant typography
Additional Notes:
The design should evoke the emotions of a wedding day – elegance, uniqueness, style, and class. Please avoid flashy colors, excessive graphic effects, or overly decorative elements. Subtlety, prestige, and sophistication are key.

```html
<!DOCTYPE html>
<html lang="en">
<head>
<meta charset="utf-8">
<title>WestaKolory.pl – Luxury Wedding Cars</title>
<link href="https://fonts.googleapis.com/css2?family=Lexend:wght@300;400&family=Arimo:wght@400;700&display=swap" rel="stylesheet">
<style>
:root{
  --navy:#131d2b;
  --ink:#151515;
  --gold:#d6b34a;
  --price:#c9a43c;
  --grey:#f1f1f1;
  --line:#cfcfcf;
  --muted:#555;
  --white:#fff;
}
*{margin:0;padding:0;box-sizing:border-box}
html,body{width:1200px;height:4219px;overflow:hidden;background:var(--white)}
body{font-family:"Arimo",Arial,sans-serif;color:var(--ink);position:relative}
.abs{position:absolute}
h1,h2,h3,.display{font-family:"Lexend",Arial,sans-serif;font-weight:300;text-transform:uppercase}
.section-title{font-size:34px;letter-spacing:.5px;color:var(--ink)}
.rule{width:72px;height:2px;background:var(--gold)}
.center{left:0;width:1200px;text-align:center}
.btn-dark{background:var(--navy);color:#fff;font-weight:700;font-size:14px;display:flex;align-items:center;justify-content:center;gap:12px}

/* header */
.site-header{top:0;left:0;width:1200px;height:80px;background:var(--navy);color:#fff}
.menu{left:144px;top:28px;display:flex;align-items:center;gap:14px;font-size:15px}
.brand{left:0;width:1200px;top:22px;text-align:center;font-family:"Lexend",sans-serif;font-size:26px;font-weight:300;color:var(--gold)}
.tools{right:144px;top:26px;display:flex;align-items:center;gap:22px;font-size:14px}
.lang{display:flex;align-items:center;gap:7px}
.dot{width:22px;height:22px;border-radius:50%;background:#8da2c4}

/* hero */
.hero{top:80px;left:0;width:1200px;height:640px;background:radial-gradient(ellipse at 50% 90%,#2d2f36 0%,#181615 40%,#0b0a0a 100%);color:#fff}
.hero-media{inset:0}
.hero-arrow{top:275px;width:37px;height:37px;border:1px solid #fff;display:flex;align-items:center;justify-content:center}
.eyebrow{top:155px;left:0;width:1200px;display:flex;justify-content:center;align-items:center;gap:14px;color:var(--gold);font-size:11px;font-weight:700}
.eyebrow span.ln{width:60px;height:1px;background:var(--gold)}
.hero h1{top:196px;font-size:46px;color:#fff}
.hero .sub{top:266px;font-size:16px}
.explore{top:329px;left:512px;width:176px;height:51px;border:2px solid #fff;display:flex;align-items:center;justify-content:center;gap:14px;font-weight:700;font-size:15px}
.watch{top:552px;font-size:13px}
.ticker{top:603px;left:0;width:1200px;height:37px;background:rgba(20,28,44,.8);display:flex;align-items:center;gap:36px;font-family:"Lexend",sans-serif;font-size:21px;color:#4d5668;white-space:nowrap;overflow:hidden}
.ticker i{width:20px;height:20px;border-radius:50%;background:#4d5668;display:inline-block}

/* about */
.about-title{top:790px}
.about-rule{top:855px;left:564px}
.about-text{top:878px;left:150px;width:900px;text-align:center;font-size:12.5px;line-height:23px;color:#333}
.about-text p+p{margin-top:8px}
.read-more{top:1035px;left:527px;width:144px;height:47px}

/* fleets */
.fleet-title{top:1158px;left:144px}
.fleet-rule{top:1229px;left:144px}
.nav-btn{top:1167px;width:44px;height:44px;display:flex;align-items:center;justify-content:center}
.card{top:1278px;width:282px}
.card .photo{height:225px}
.card h3{font-family:"Arimo",sans-serif;text-transform:none;font-weight:400;font-size:17px;margin:18px 0 0 13px;white-space:nowrap}
.card .price{color:var(--price);font-weight:700;font-size:18px;margin:12px 0 0 13px}
.card.featured{box-shadow:0 2px 14px rgba(0,0,0,.14);padding:8px;top:1270px;width:298px;height:326px;left:452px}

/* services */
.services-title{top:1675px}
.services-rule{top:1747px;left:564px}
.band{left:0;width:1200px;height:280px;color:#fff}
.band h3{position:absolute;top:55px;font-size:22px}
.band p{position:absolute;top:148px;width:440px;font-size:12.5px;line-height:23px}

/* why */
.why-media{top:2626px;left:0;width:601px;height:478px;background:linear-gradient(135deg,#a9a9ad,#4a4d52 55%,#2e3b32)}
.why{top:2626px;left:601px;width:599px;height:478px;background:var(--grey)}
.why h2{position:absolute;left:52px;top:72px;font-size:34px}
.why .rule{position:absolute;left:52px;top:134px}
.why ul{position:absolute;left:52px;top:166px;list-style:none}
.why li{height:65px}
.why li b{display:flex;align-items:center;gap:7px;font-family:"Lexend",sans-serif;font-weight:300;font-size:16px}
.why li span{display:block;font-size:12px;margin-top:10px;color:#333}

/* faq */
.faq-title{top:3176px}
.faq-rule{top:3238px;left:564px}
.faq-row{left:144px;width:912px;height:44px;border-bottom:1px solid #888;font-size:14px}
.faq-row .num{position:absolute;left:0;top:0;width:26px;height:26px;background:var(--navy);color:#fff;font-size:13px;font-weight:700;display:flex;align-items:center;justify-content:center}
.faq-row .q{position:absolute;left:41px;top:5px}
.faq-row .type{position:absolute;left:511px;top:5px;font-size:13px}
.faq-row .sep{position:absolute;left:637px;top:2px;width:1px;height:24px;background:#999}
.faq-row .cat{position:absolute;left:701px;top:5px;font-size:13px}
.faq-row .plus{position:absolute;right:0;top:3px}
.faq-open{left:144px;top:3464px;width:912px;height:108px;background:#f2f2f2}
.faq-open .num{background:var(--gold);color:var(--ink)}
.faq-open .answer{position:absolute;left:41px;top:54px;width:820px;font-size:12.5px;line-height:23px;color:#666}
.more-q{top:3706px;left:507px;width:185px;height:48px}

/* footer */
.site-footer{top:3826px;left:0;width:1200px;height:393px;background:var(--navy);color:#fff}
.foot-brand{left:144px;top:46px;font-family:"Lexend",sans-serif;font-weight:300;font-size:26px;color:var(--gold);display:flex;align-items:center;gap:10px}
.foot-brand i{width:14px;height:14px;border-radius:50%;background:var(--gold)}
.foot-nav{right:144px;top:64px;display:flex;gap:10px;font-size:13.5px}
.foot-nav .active{color:var(--gold)}
.foot-col h4{font-family:"Lexend",sans-serif;font-weight:300;font-size:16px;text-transform:uppercase;margin-bottom:16px}
.foot-col ul{list-style:none;font-size:12.5px}
.foot-col li{height:24.5px;display:flex;gap:12px}
.foot-col li::before{content:"»";color:var(--gold)}
.contact li{height:33px;gap:12px}
.contact li::before{content:none}
.pay{left:144px;top:316px;display:flex;gap:4px}
.pay span{width:31px;height:21px;border-radius:2px}
.social{left:913px;top:270px;display:flex;gap:8px}
.social span{width:28px;height:28px;background:#fff}
.social span.on{background:var(--gold)}
.copy{top:358px;font-size:11px}
</style>
</head>
<body>

<header class="site-header abs">
  <div class="menu abs">
    <svg width="22" height="16" viewBox="0 0 22 16"><path d="M1 2h20M1 8h20M1 14h12" stroke="#fff" stroke-width="2"/></svg>
    <span>Menu</span>
  </div>
  <div class="brand abs">WestaKolory</div>
  <div class="tools abs">
    <span class="lang"><span class="dot"></span>EN
      <svg width="9" height="6" viewBox="0 0 9 6"><path d="M1 1l3.5 3.5L8 1" stroke="#fff" fill="none" stroke-width="1.4"/></svg></span>
    <svg width="22" height="20" viewBox="0 0 24 22"><path d="M12 20S2 13.5 2 7.3A5 5 0 0 1 12 5a5 5 0 0 1 10 2.3C22 13.5 12 20 12 20z" fill="none" stroke="#fff" stroke-width="1.8"/></svg>
    <svg width="20" height="22" viewBox="0 0 20 22"><circle cx="10" cy="6" r="4.5" fill="none" stroke="#fff" stroke-width="1.8"/><path d="M2 21c0-5 3.5-8 8-8s8 3 8 8" fill="none" stroke="#fff" stroke-width="1.8"/></svg>
    <svg width="22" height="20" viewBox="0 0 24 22"><path d="M1 2h4l3 12h12l3-9H7" fill="none" stroke="#fff" stroke-width="1.8"/><circle cx="9" cy="19" r="1.8" fill="#fff"/><circle cx="19" cy="19" r="1.8" fill="#fff"/></svg>
  </div>
</header>

<section class="hero abs">
  <div class="hero-media abs" role="img" aria-label="Black luxury limousine parked at night in front of a lit hotel entrance"></div>
  <div class="hero-arrow abs" style="left:74px"><svg width="10" height="14" viewBox="0 0 10 14"><path d="M7 2L2 7l5 5" stroke="#fff" fill="none" stroke-width="1.6"/></svg></div>
  <div class="hero-arrow abs" style="left:1089px"><svg width="10" height="14" viewBox="0 0 10 14"><path d="M3 2l5 5-5 5" stroke="#fff" fill="none" stroke-width="1.6"/></svg></div>
  <div class="eyebrow abs"><span class="ln"></span>WELCOME TO WESTA KOLORY<span class="ln"></span></div>
  <h1 class="abs center">Luxury Wedding Cars</h1>
  <p class="sub abs center">Rent a Limousine or a Premium class Van With a Chauffeur</p>
  <div class="explore abs">Explore Cars
    <svg width="20" height="14" viewBox="0 0 20 14"><path d="M1 7h17M12 1l6 6-6 6" stroke="#fff" fill="none" stroke-width="2"/></svg></div>
  <p class="watch abs center"><span style="color:var(--gold)">▶</span> Watch Video</p>
  <div class="ticker abs">
    <span>MOUSINE</span><i></i><span>SPORTS CARS</span><i></i><span>PREMIUM VAN</span><i></i><span>PREMIUM CLASS</span>
  </div>
</section>

<h2 class="section-title abs center about-title">About Us</h2>
<div class="rule abs about-rule"></div>
<div class="about-text abs">
  <p>WestyKolory.pl was created out of a genuine love for exceptional cars. We started as two young enthusiasts with a deep appreciation for vehicles that offer more than just performance – cars that create atmosphere, emotion, and presence. Over time, our private collection evolved into a premium chauffeur-driven service dedicated to weddings and refined celebrations.</p>
  <p>Every car we offer is privately owned and maintained with the greatest care. We're not a typical rental company and never will be. What we deliver is personal, dedicated, and above all Uncompromising.</p>
</div>
<div class="btn-dark read-more abs">Read More
  <svg width="18" height="12" viewBox="0 0 18 12"><path d="M1 6h15M11 1l5 5-5 5" stroke="#fff" fill="none" stroke-width="1.8"/></svg></div>

<h2 class="section-title abs fleet-title">Our Fleets</h2>
<div class="rule abs fleet-rule"></div>
<div class="nav-btn abs" style="left:954px;background:#eee"><svg width="20" height="14" viewBox="0 0 20 14"><path d="M19 7H2M8 1L2 7l6 6" stroke="#222" fill="none" stroke-width="1.8"/></svg></div>
<div class="nav-btn abs" style="left:1010px;background:var(--navy)"><svg width="20" height="14" viewBox="0 0 20 14"><path d="M1 7h17M12 1l6 6-6 6" stroke="var(--gold)" fill="none" stroke-width="1.8"/></svg></div>

<article class="card abs" style="left:144px;width:280px">
  <div class="photo" role="img" aria-label="Silver Corvash Solenne GT Sport coupe" style="background:linear-gradient(135deg,#d9d9dc,#9ea3aa 60%,#5e5f61)"></div>
  <h3>Corvash Solenne GT Sport</h3>
  <p class="price">2,500.00zł</p>
</article>
<article class="card featured abs">
  <div class="photo" role="img" aria-label="Grey Halvor RX SUV at sunset" style="background:linear-gradient(160deg,#c7b49a,#5f6168 50%,#2e3036)"></div>
  <h3>Halvor RX</h3>
  <p class="price">5,500.00zł</p>
</article>
<article class="card abs" style="left:774px">
  <div class="photo" role="img" aria-label="Light blue Elbrin Tusko Vantor sports car under a modern canopy" style="background:linear-gradient(160deg,#5a6e95,#b27a4a 45%,#2e4f73)"></div>
  <h3>Elbrin Tusko Vantor</h3>
  <p class="price">1,500.00zł</p>
</article>

<h2 class="section-title abs center services-title">Our Services</h2>
<div class="rule abs services-rule"></div>

<section class="band abs" style="top:1786px;background:linear-gradient(90deg,#8e8e8f,#b4b3b1 45%,#a2a19f)" role="img" aria-label="Bride and groom embracing by the sea">
  <h3 style="left:144px">Weddings</h3>
  <p style="left:625px">Lorem ipsum dolor sit amet, consectetur adipiscing elit, sed do eiusmod tempor incididunt ut labore et dolore magna aliqua. Ut enim ad minim veniam, quis nostrud exercitation ullamco laboris</p>
</section>
<section class="band abs" style="top:2066px;background:linear-gradient(90deg,#2f2b27,#5b4a3c 55%,#231f1c)" role="img" aria-label="Photo shoot team working in a studio">
  <h3 style="right:144px">Photo Shoots</h3>
  <p style="left:144px">Lorem ipsum dolor sit amet, consectetur adipiscing elit, sed do eiusmod tempor incididunt ut labore et dolore magna aliqua. Ut enim ad minim veniam, quis nostrud exercitation ullamco laboris</p>
</section>
<section class="band abs" style="top:2346px;background:linear-gradient(90deg,#1d2d45,#314866 45%,#1a2940)" role="img" aria-label="Film reel and film strip on a blue background">
  <h3 style="left:144px">Film Rental</h3>
  <p style="left:625px">Lorem ipsum dolor sit amet, consectetur adipiscing elit, sed do eiusmod tempor incididunt ut labore et dolore magna aliqua. Ut enim ad minim veniam, quis nostrud exercitation ullamco laboris</p>
</section>

<div class="why-media abs" role="img" aria-label="Chrome grille of a classic wedding car decorated with a white ribbon"></div>
<section class="why abs">
  <h2>Why Us?</h2>
  <div class="rule"></div>
  <ul>
    <li><b><svg width="14" height="14" viewBox="0 0 14 14"><circle cx="7" cy="7" r="7" fill="#111"/><path d="M4 7l2 2 4-4" stroke="#fff" fill="none" stroke-width="1.6"/></svg>LOGISTICS</b><span>We can deliver the car to your desired place no need to waste time.</span></li>
    <li><b><svg width="14" height="14" viewBox="0 0 14 14"><circle cx="7" cy="7" r="7" fill="#111"/><path d="M4 7l2 2 4-4" stroke="#fff" fill="none" stroke-width="1.6"/></svg>EASY CAR RENT</b><span>Everything is set online - all documents are digital.</span></li>
    <li><b><svg width="14" height="14" viewBox="0 0 14 14"><circle cx="7" cy="7" r="7" fill="#111"/><path d="M4 7l2 2 4-4" stroke="#fff" fill="none" stroke-width="1.6"/></svg>24H SERVICE</b><span>Optional secondary info block text</span></li>
    <li><b><svg width="14" height="14" viewBox="0 0 14 14"><circle cx="7" cy="7" r="7" fill="#111"/><path d="M4 7l2 2 4-4" stroke="#fff" fill="none" stroke-width="1.6"/></svg>SECURE SHOPPING</b><span>Our website uses the Best Security practices!</span></li>
  </ul>
</section>

<h2 class="section-title abs center faq-title">Frequently Asked Questions</h2>
<div class="rule abs faq-rule"></div>

<div class="faq-row abs" style="top:3302px">
  <span class="num">01</span><span class="q">Lorem ipsum dolor sit amet, consectetur adipiscing elit?</span>
  <span class="type">Articals</span><span class="sep"></span><span class="cat">Wedding</span>
  <svg class="plus" width="18" height="18" viewBox="0 0 18 18"><path d="M9 1v16M1 9h16" stroke="#111" stroke-width="1.8"/></svg>
</div>
<div class="faq-row abs" style="top:3385px">
  <span class="num">02</span><span class="q">Lorem ipsum dolor sit amet, consectetur adipiscing elit?</span>
  <span class="type">Articals</span><span class="sep"></span><span class="cat">Photo Shoot</span>
  <svg class="plus" width="18" height="18" viewBox="0 0 18 18"><path d="M9 1v16M1 9h16" stroke="#111" stroke-width="1.8"/></svg>
</div>
<div class="faq-row faq-open abs" style="border:none">
  <span class="num" style="top:4px">03</span><span class="q" style="top:9px">Lorem ipsum dolor sit amet, consectetur adipiscing elit?</span>
  <span class="type" style="top:9px">Articals</span><span class="sep" style="top:6px"></span><span class="cat" style="top:9px">Film Rental</span>
  <svg class="plus" style="top:12px" width="18" height="4" viewBox="0 0 18 4"><path d="M1 2h16" stroke="var(--gold)" stroke-width="1.8"/></svg>
  <p class="answer">Duis aute irure dolor in reprehenderit in voluptate velit esse cillum dolore eu fugiat nulla pariatur. Excepteur sint occaecat cupidatat non proident, sunt in culpa qui officia deserunt mollit anim id est laborumv oluptatem accusantium dolorem</p>
</div>
<div class="faq-row abs" style="top:3623px">
  <span class="num">04</span><span class="q">Lorem ipsum dolor sit amet, consectetur adipiscing elit?</span>
  <span class="type">Articals</span><span class="sep"></span><span class="cat">Wedding</span>
  <svg class="plus" width="18" height="18" viewBox="0 0 18 18"><path d="M9 1v16M1 9h16" stroke="#111" stroke-width="1.8"/></svg>
</div>
<div class="btn-dark more-q abs">More Questions
  <svg width="18" height="12" viewBox="0 0 18 12"><path d="M1 6h15M11 1l5 5-5 5" stroke="#fff" fill="none" stroke-width="1.8"/></svg></div>

<footer class="site-footer abs">
  <div class="foot-brand abs"><i></i>WestaKolory</div>
  <nav class="foot-nav abs">
    <span class="active">Home</span>|<span>Services</span>|<span>About Us</span>|<span>Fleet Overview</span>|<span>Individual Car</span>|<span>Why Us</span>|<span>FAQ</span>|<span>Contact</span>
  </nav>
  <div class="foot-col contact abs" style="left:144px;top:154px">
    <h4>Contact Us</h4>
    <ul>
      <li><svg width="13" height="13" viewBox="0 0 24 24"><path d="M6 2l4 4-2 3a12 12 0 0 0 7 7l3-2 4 4-3 4C10 22 2 14 2 5z" fill="var(--gold)"/></svg>510 300 144</li>
      <li><svg width="14" height="11" viewBox="0 0 14 11"><rect width="14" height="11" fill="var(--gold)"/><path d="M0 0l7 6 7-6" stroke="var(--navy)" fill="none"/></svg>info@westakolory.pl</li>
      <li><svg width="11" height="15" viewBox="0 0 11 15"><path d="M5.5 15S0 8.5 0 5.5a5.5 5.5 0 0 1 11 0C11 8.5 5.5 15 5.5 15z" fill="var(--gold)"/><circle cx="5.5" cy="5.5" r="2" fill="var(--navy)"/></svg>Duis aute irure dolor NSW 112345</li>
    </ul>
  </div>
  <div class="foot-col abs" style="left:480px;top:154px">
    <h4>My Account</h4>
    <ul><li>Login</li><li>Order History</li><li>Affiliates</li><li>Newsletter</li><li>Gift Certificate</li><li>Returns</li></ul>
  </div>
  <div class="foot-col abs" style="left:678px;top:154px">
    <h4>Customer Service</h4>
    <ul><li>Store Locations</li><li>Our Brands</li><li>Site Map</li><li>Delivery Information</li><li>Unlimited Links</li></ul>
  </div>
  <div class="foot-col abs" style="left:913px;top:154px">
    <h4>Quick Links</h4>
    <ul><li>Privacy Policy</li><li>Terms &amp; Conditions</li></ul>
  </div>
  <div class="social abs"><span></span><span class="on"></span></div>
  <div class="pay abs">
    <span style="background:#3b74c9"></span><span style="background:#e6e6e6"></span><span style="background:#f4f4f4"></span><span style="background:#f2f2f2"></span><span style="background:#fff"></span><span style="background:#6a43d6"></span>
  </div>
  <p class="copy abs center">© 2025 Westa Kolory &nbsp;-&nbsp; All Rights Reserved</p>
</footer>

</body>
</html>
```